Letter design, envelope design, and more

Hello, we the Tavrin Gmbh are looking for our shop. Letter C5. Design does not have to be like a business card, so it can have straight lines. Only the color is important. The logo is the text under TaVRin omit.It should not be playful but Profesionel

Font styles to use
Sans Serif

Colors
0555a3
3176b5
85abd2
85cae6
34a7d8
0792cd
cee9f5
cfdfed
000000

Requirements
Must have
• Color like business card, Please, with the text under TaVRin, Correct address Lindmattstr. 4 Zip code 9517 Goldach, as well as Couvert Without addressing only design and logo with TaVrn
Nice to have
• more writing articles
Should not have
• Not too colored, Text under TaVRin, bright colors

```html
<!DOCTYPE html>
<html lang="de">
<head>
<meta charset="utf-8">
<title>Tavrin Gmbh – Briefpapier und Couvert</title>
<link rel="stylesheet" href="https://fonts.googleapis.com/css2?family=Roboto:wght@400;700&display=swap">
<style>
  :root {
    --brand: #0555a3;
    --brand-mid: #3176b5;
    --brand-soft: #85abd2;
    --brand-pale: #cfdfed;
    --paper: #f4f5f7;
    --backdrop: #d2d2d2;
    --ink: #3c3c3c;
    --white: #ffffff;
  }
  * { box-sizing: border-box; margin: 0; padding: 0; }
  html, body { width: 1200px; height: 810px; overflow: hidden; }
  body {
    background: var(--backdrop);
    font-family: "Roboto", Arial, sans-serif;
    color: var(--ink);
    position: relative;
  }
  .sheet {
    position: absolute;
    background: var(--paper);
    overflow: hidden;
  }
  .letterhead { left: 137px; top: 110px; width: 436px; height: 614px; }
  .envelope-back { left: 619px; top: 193px; width: 444px; height: 222px; }
  .envelope-front { left: 618px; top: 444px; width: 445px; height: 221px; }

  .brand {
    position: absolute;
    display: flex;
    align-items: center;
    gap: 6px;
    font-weight: 700;
    color: var(--brand);
    letter-spacing: 0.5px;
    white-space: nowrap;
  }
  .brand-square { background: var(--brand); display: block; }
  .letterhead .brand { left: 41px; top: 58px; font-size: 18px; }
  .letterhead .brand-square { width: 14px; height: 14px; }
  .envelope-front .brand { left: 32px; top: 41px; font-size: 16px; }
  .envelope-front .brand-square { width: 12px; height: 12px; }

  .contact {
    position: absolute;
    font-style: normal;
    font-size: 7px;
    line-height: 10px;
    color: var(--ink);
    white-space: nowrap;
  }
  .letterhead .contact { left: 332px; top: 46px; }
  .envelope-front .contact { left: 32px; top: 73px; }
  .contact .gap { height: 4px; }
  .contact-line { display: flex; align-items: center; gap: 4px; }
  .contact-line svg { width: 8px; height: 7px; flex: none; }

  .footer-wave {
    position: absolute;
    left: 0; bottom: 0;
    width: 100%;
  }
  .letterhead .footer-wave { height: 36px; }
  .envelope-front .footer-wave { height: 40px; }
  .web {
    position: absolute;
    color: var(--white);
    font-size: 7.5px;
    right: 37px;
    bottom: 9px;
  }

  .flap {
    position: absolute;
    left: 0; top: 0;
    width: 444px; height: 66px;
  }
  .flap-name {
    position: absolute;
    left: 0; right: 0; top: 24px;
    text-align: center;
    color: var(--white);
    font-weight: 700;
    font-size: 15px;
    letter-spacing: 1px;
  }
</style>
</head>
<body>

<section class="sheet letterhead" aria-label="Briefbogen">
  <div class="brand"><span class="brand-square"></span>TAVRIN GMBH</div>
  <address class="contact">
    <div>Lindmattstr. 4</div>
    <div>9517 Goldach</div>
    <div class="gap"></div>
    <div class="contact-line">
      <svg viewBox="0 0 8 7"><path d="M1 6 C1 2 3 1 6 1 L7 2 L5.6 3 C4 3 3 4 3 5.5 L2 6.5 Z" fill="var(--brand)"/></svg>
      +41 71 555 24 80
    </div>
    <div class="contact-line">
      <svg viewBox="0 0 8 7"><rect x="0.5" y="1" width="7" height="5" fill="var(--brand)"/><path d="M0.5 1 L4 4 L7.5 1" stroke="var(--white)" stroke-width="0.8" fill="none"/></svg>
      info@tavrin.ch
    </div>
  </address>
  <svg class="footer-wave" viewBox="0 0 436 36" preserveAspectRatio="none">
    <path d="M0 0 C90 14 170 28 260 14 C330 3 390 0 436 2 L436 36 L0 36 Z" fill="var(--brand-soft)"/>
    <path d="M0 12 C100 28 180 34 270 20 C340 9 395 10 436 14 L436 36 L0 36 Z" fill="var(--white)"/>
    <path d="M0 15 C100 31 180 37 270 23 C340 12 395 13 436 17 L436 36 L0 36 Z" fill="var(--brand)"/>
  </svg>
  <div class="web">www.tavrin.ch</div>
</section>

<section class="sheet envelope-back" aria-label="Couvert Rückseite">
  <svg class="flap" viewBox="0 0 444 66">
    <path d="M0 0 L444 0 L435 56 Q433 65 424 65 L20 65 Q11 65 9 56 Z" fill="var(--brand)"/>
  </svg>
  <div class="flap-name">TAVRIN</div>
</section>

<section class="sheet envelope-front" aria-label="Couvert Vorderseite">
  <div class="brand"><span class="brand-square"></span>TAVRIN GMBH</div>
  <address class="contact">
    <div>Lindmattstr. 4</div>
    <div>9517 Goldach</div>
    <div class="gap"></div>
    <div class="contact-line">
      <svg viewBox="0 0 8 7"><path d="M1 6 C1 2 3 1 6 1 L7 2 L5.6 3 C4 3 3 4 3 5.5 L2 6.5 Z" fill="var(--brand)"/></svg>
      +41 71 555 24 80
    </div>
    <div class="contact-line">
      <svg viewBox="0 0 8 7"><rect x="0.5" y="1" width="7" height="5" fill="var(--brand)"/><path d="M0.5 1 L4 4 L7.5 1" stroke="var(--white)" stroke-width="0.8" fill="none"/></svg>
      info@tavrin.ch
    </div>
  </address>
  <svg class="footer-wave" viewBox="0 0 445 40" preserveAspectRatio="none">
    <path d="M0 2 C90 18 170 32 260 16 C330 4 390 0 445 2 L445 40 L0 40 Z" fill="var(--brand-soft)"/>
    <path d="M0 14 C100 32 180 38 270 22 C340 10 395 10 445 16 L445 40 L0 40 Z" fill="var(--white)"/>
    <path d="M0 17 C100 35 180 41 270 25 C340 13 395 13 445 19 L445 40 L0 40 Z" fill="var(--brand)"/>
  </svg>
  <div class="web">www.tavrin.ch</div>
</section>

</body>
</html>
```